Velk Partners Building Business Cards

We need a business card that reflects our business as "Solar Experts" in San Diego. Browse our website www.velkpartners.example our License needs to be displayed as "CSLB# 3867140" our phone number is (619) 555-0187

Save thousands on your electric bills and increase the value of your home while helping to protect the environment. Our solar installation experts will help you design the system that's right for you, using only the highest quality equipment that will look great and give you ideal performance. Our goal is to make you energy independent, and get your electric bill to 0.

Paul Osterby
(619) 555-0187
paul@velkpartners.example

Target Market(s)

Home owners in san diego looking for solar

Industry/Entity Type

Solar Energy

Contact Information for Business Card

Paul Osterby
(619) 555-0187
paul@velkpartners.example

Font styles to use
Other font styles liked:
• Use our logo font

Requirements
Must have
• License needs to be displayed as "CSLB# 3867140" our phone number is (619) 555-0187
Nice to have
• Real images of rooftop home solar in san diego
Should not have
• our business address

```html
<!DOCTYPE html>
<html lang="en">
<head>
<meta charset="utf-8">
<title>Velk Partners Building – Business Card</title>
<link rel="stylesheet" href="https://fonts.googleapis.com/css2?family=Open+Sans:ital,wght@0,400;0,600;0,700;1,400&display=swap">
<style>
  :root {
    --backdrop: #4f4f4f;
    --card-white: #ffffff;
    --navy: #1a3d78;
    --sun-gold: #f7ae00;
    --sun-pale: #fde7a6;
    --ink-grey: #555555;
    --radius: 22px;
  }
  * { box-sizing: border-box; margin: 0; padding: 0; }
  html, body {
    width: 1105px; height: 1200px; overflow: hidden;
    background: var(--backdrop);
    font-family: "Open Sans", Arial, sans-serif;
  }
  .canvas { position: relative; width: 1105px; height: 1200px; }
  .card {
    position: absolute; left: 193px; width: 718px; height: 410px;
    border-radius: var(--radius); overflow: hidden;
    background: var(--card-white);
  }
  .card--front { top: 167px; }
  .card--back { top: 623px; }

  .sunrise-art {
    position: absolute; left: 0; top: 0; width: 100%; height: 258px;
    background: linear-gradient(180deg, var(--card-white) 0%, var(--sun-pale) 60%, var(--sun-gold) 100%);
  }
  .contact-band {
    position: absolute; left: 0; top: 258px; width: 100%; height: 152px;
    background: var(--navy);
  }
  .holder { position: absolute; left: 35px; bottom: 22px; }
  .holder__name { color: var(--card-white); font-weight: 600; font-size: 25px; line-height: 1.1; }
  .holder__title { color: var(--sun-gold); font-size: 20px; line-height: 1.3; }

  .contact-list {
    position: absolute; right: 36px; top: 16px; list-style: none;
    color: var(--card-white); font-size: 18px; text-align: right;
  }
  .contact-list li { display: flex; justify-content: flex-end; align-items: center; gap: 8px; height: 28px; }
  .contact-list .licence { margin-right: 0; }
  .contact-list svg { width: 18px; height: 18px; flex: none; }

  .brand-name {
    position: absolute; left: 0; right: 0; top: 180px;
    text-align: center; color: var(--navy);
    font-weight: 700; font-size: 46px; letter-spacing: -0.5px;
  }
  .brand-web {
    position: absolute; left: 0; right: 0; top: 334px;
    text-align: center; color: var(--ink-grey);
    font-style: italic; font-size: 19px; letter-spacing: 6px;
  }
</style>
</head>
<body>
<main class="canvas">
  <section class="card card--front" aria-label="Business card front">
    <div class="sunrise-art" role="img" aria-label="Illustration of a rising sun over rolling waves in gold and navy"></div>
    <div class="contact-band">
      <ul class="contact-list">
        <li class="licence">CSLB# 3867140</li>
        <li>(619) 555-0187
          <svg viewBox="0 0 20 20" aria-hidden="true"><path fill="#f7ae00" d="M4 2l3 0 2 4-2 2c1 2 3 4 5 5l2-2 4 2 0 3c0 1-1 2-2 2C9 18 2 11 2 4c0-1 1-2 2-2z"/></svg>
        </li>
        <li>paul@velkpartners.example
          <svg viewBox="0 0 20 20" aria-hidden="true"><rect x="2" y="5" width="16" height="11" fill="#f7ae00"/><path d="M2 5l8 6 8-6" fill="none" stroke="#1a3d78" stroke-width="1.5"/></svg>
        </li>
        <li>www.velkpartners.example
          <svg viewBox="0 0 20 20" aria-hidden="true"><circle cx="10" cy="10" r="8" fill="#f7ae00"/><path d="M2 10h16M10 2c-3 3-3 13 0 16M10 2c3 3 3 13 0 16" fill="none" stroke="#1a3d78" stroke-width="1.3"/></svg>
        </li>
      </ul>
      <div class="holder">
        <p class="holder__name">Paul Osterby</p>
        <p class="holder__title">CEO/Founder</p>
      </div>
    </div>
  </section>

  <section class="card card--back" aria-label="Business card back">
    <p class="brand-name">Velk Partners Building</p>
    <p class="brand-web">www.velkpartners.example</p>
  </section>
</main>
</body>
</html>
```